Fitness Equipment & Service

I want to make the card eye catching and fun. We are called Corvane Motion Limited and we are based in Wales. We sell, install and service all types of fitness equipment from Skipping ropes, right through the Dumbbells, Kettle bells and Barbells through to state of the art Treadmills, Running Machines and Strength Equipment. We also design and install changing room furniture and lockers.

TYPOGRAPHY
We would like to use Futrura. Futura has an appearance of efficiency and forwardness. The typeface is derived
from simple geometric forms (near-perfect circles, triangles and squares) and is based on strokes of
near-even weight, which are low in contrast. This is most visible in the almost perfectly round stroke of
the o, which is nonetheless slightly ovoid.
The lowercase has tall ascenders, which rise above the cap line. The uppercase
characters present proportions similar to those of classical Roman capitals.

TYPOGRAPHIC CONSIDERATIONS
No Strike though
No Horizontal Scaling
No Drop Shadows
No Effects
Never use less than 120% Leading

OUR CORPORATE COLOURS
BRAND GUIDELINES
We were thinking that our primary colour palette consists of the Acid Green (Pantone 382) and Process Black.

We work closely with tquarly Ltd and would like to include their name on the card somewhere. I have attached images of the other brands that we work with as an idea or the small icons I have included that illustrate what we do?. I have very kindly been given permission to use any of the images off the files that I have included below, so I hope these help. I will include these below. I would be open to suggestions if it made the card more striking Can you do it?
Updates

Hi All, Just wanted to add a few thoughts but you are the guys with the creative visions (thats why are here) We are based in Wales, UK and we would be open to lots of different ideas on a theme but must be eye catching, Bold and FUN. If you can or think that the Welsh or any dragon could be put in there then go for it (its not a must have) We have also added some ideas for colour but again its over to you!! GO FOR IT ! Thanks and look forward to your visions! Owen

Hi All, Just thought I would sen through the contact details that need to be on the card. (if you want to play around with icons instead of the wording twitter, Facebook, go for it): Corvane Motion Limited Owen Pritchard Managing Director Mob: +44 (0)7582 913 406 e-mail: sales@corvanemotion.co.uk Web: Corvanemotion.co.uk twitter: @motionLetterbin Facebook: Corvane Motion Limited

```html
<!DOCTYPE html>
<html lang="en">
<head>
<meta charset="utf-8">
<title>Corvane Motion Limited – Business Card</title>
<link rel="stylesheet" href="https://fonts.googleapis.com/css2?family=Arimo:wght@400;700&display=swap">
<style>
  :root {
    --page-bg: #e9e6e1;
    --navy-deep: #0d1f4f;
    --navy: #1b3a86;
    --navy-light: #2c55b0;
    --gold: #c49a3a;
    --gold-light: #e2c070;
    --ink: #0a0a0a;
    --paper: #ffffff;
    --text-light: #f3f5fb;
  }
  * { margin: 0; padding: 0; box-sizing: border-box; }
  html, body {
    width: 1200px;
    height: 950px;
    overflow: hidden;
    background: var(--page-bg);
    font-family: "Arimo", Arial, sans-serif;
  }
  .sheet {
    position: relative;
    width: 1200px;
    height: 950px;
  }
  .card {
    position: absolute;
    left: 240px;
    width: 720px;
    height: 411px;
    overflow: hidden;
    box-shadow: 0 6px 18px rgba(0,0,0,0.18);
  }
  .card--back {
    top: 50px;
    background: radial-gradient(ellipse at 45% 40%, var(--navy-light) 0%, var(--navy) 45%, var(--navy-deep) 100%);
  }
  .card--front {
    top: 501px;
    background: var(--paper);
  }
  .card__art {
    position: absolute;
    inset: 0;
    width: 100%;
    height: 100%;
  }

  /* back side */
  .back-mark {
    position: absolute;
    left: 50%;
    top: 88px;
    transform: translateX(-50%);
    display: flex;
    flex-direction: column;
    align-items: center;
    gap: 18px;
  }
  .back-mark__circle {
    width: 130px;
    height: 130px;
    border-radius: 50%;
    background: var(--navy-deep);
    border: 4px solid #9aa8c8;
  }
  .back-mark__name {
    color: var(--text-light);
    font-size: 22px;
    font-weight: 700;
    letter-spacing: 1px;
    text-transform: uppercase;
  }
  .back-url {
    position: absolute;
    right: 150px;
    top: 290px;
    color: var(--text-light);
    font-size: 15px;
    letter-spacing: 1.5px;
  }
  .back-url::after {
    content: "";
    display: inline-block;
    width: 60px;
    height: 1px;
    margin-left: 6px;
    vertical-align: middle;
    background: var(--text-light);
  }

  /* front side */
  .brand {
    position: absolute;
    left: 44px;
    top: 34px;
    display: flex;
    flex-direction: column;
    align-items: flex-start;
    gap: 14px;
  }
  .brand__circle {
    width: 110px;
    height: 110px;
    margin-left: 30px;
    border-radius: 50%;
    background: var(--navy);
    border: 3px solid #c9d0e0;
  }
  .brand__name {
    color: var(--navy-deep);
    font-size: 19px;
    font-weight: 700;
    letter-spacing: 0.5px;
    text-transform: uppercase;
    line-height: 1.25;
  }
  .contact {
    position: absolute;
    right: 34px;
    top: 112px;
    text-align: right;
    color: var(--text-light);
    font-size: 15px;
    line-height: 1.32;
  }
  .contact__name {
    font-size: 22px;
    font-weight: 700;
    line-height: 1.25;
  }
  .contact__role {
    font-size: 16px;
    margin-bottom: 4px;
  }
  .contact__line {
    display: flex;
    justify-content: flex-end;
    align-items: center;
    gap: 8px;
  }
  .contact__icon {
    width: 14px;
    height: 14px;
    flex: none;
  }
  .contact__icon--dot { border-radius: 50%; background: var(--text-light); }
  .contact__icon--square { border-radius: 2px; background: var(--text-light); }
</style>
</head>
<body>
<main class="sheet">

  <section class="card card--back" aria-label="Card back">
    <div class="back-mark">
      <div class="back-mark__circle"></div>
      <div class="back-mark__name">Corvane Motion Limited</div>
    </div>
    <div class="back-url">Corvanemotion.co.uk</div>
  </section>

  <section class="card card--front" aria-label="Card front">
    <svg class="card__art" viewBox="0 0 720 411" preserveAspectRatio="none" aria-hidden="true">
      <defs>
        <linearGradient id="frontBlue" x1="0" y1="0" x2="1" y2="1">
          <stop offset="0" stop-color="#2c55b0"/>
          <stop offset="0.55" stop-color="#1b3a86"/>
          <stop offset="1" stop-color="#0d1f4f"/>
        </linearGradient>
        <linearGradient id="goldBand" x1="0" y1="1" x2="1" y2="0">
          <stop offset="0" stop-color="#a97f28"/>
          <stop offset="0.5" stop-color="#e2c070"/>
          <stop offset="1" stop-color="#c49a3a"/>
        </linearGradient>
      </defs>
      <polygon class="front-panel" points="110,411 590,0 720,0 720,411" fill="url(#frontBlue)"/>
      <polygon class="front-rule" points="66,411 568,0 573,0 74,411" fill="#0a0a0a"/>
      <polygon class="front-band" points="86,411 578,0 590,0 110,411" fill="url(#goldBand)"/>
    </svg>

    <div class="brand">
      <div class="brand__circle"></div>
      <div class="brand__name">Corvane Motion<br>Limited</div>
    </div>

    <div class="contact">
      <div class="contact__name">Owen Pritchard</div>
      <div class="contact__role">Managing Director</div>
      <div class="contact__line">27 Tarrow Lane</div>
      <div class="contact__line">Brynmor, CF31 4QX</div>
      <div class="contact__line">+44 (0)7582 913 406
        <svg class="contact__icon" viewBox="0 0 14 14" aria-hidden="true"><rect x="3" y="0.5" width="8" height="13" rx="1.5" fill="none" stroke="#f3f5fb" stroke-width="1.4"/><circle cx="7" cy="11" r="0.9" fill="#f3f5fb"/></svg>
      </div>
      <div class="contact__line">sales@corvanemotion.co.uk
        <svg class="contact__icon" viewBox="0 0 14 14" aria-hidden="true"><rect x="0.5" y="2.5" width="13" height="9" fill="#f3f5fb"/><path d="M0.5 2.5 L7 7.5 L13.5 2.5" fill="none" stroke="#1b3a86" stroke-width="1.2"/></svg>
      </div>
      <div class="contact__line">Corvanemotion.co.uk <span class="contact__icon contact__icon--dot"></span></div>
      <div class="contact__line">@motionLetterbin <span class="contact__icon contact__icon--square"></span></div>
      <div class="contact__line">Corvane Motion Limited <span class="contact__icon contact__icon--square"></span></div>
    </div>
  </section>

</main>
</body>
</html>
```